Spring Detox sale graphics for social media

You MUST read the Brief in the WORD document and follow the instructions there. I want to create 10 social media graphics (new Instagram size 4:5 (1080 x 1350 pixels) focusing on our Mother’s Day Spring Detox Sale graphics, using any of the pics attached. Use the attached pics, NO RANDOM STOCK PHOTOGRAPHY. For the color scheme of the graphics, they should all be complementary to the product colors or feel like Spring time.

Target Market(s)

primarily women

Requirements
Must have
• the photos and text attached

```html
<!DOCTYPE html>
<html lang="en">
<head>
<meta charset="utf-8">
<title>Mother's Day Spring Detox Sale</title>
<link rel="stylesheet" href="https://fonts.googleapis.com/css2?family=Montserrat:wght@400;600;700&family=Crimson+Text:wght@400&display=swap">
<style>
  :root {
    --plum: #6b3560;
    --orchid: #bd53b6;
    --orchid-light: #d67fd2;
    --lilac-line: #e6c8e6;
    --paper: #ffffff;
  }
  html, body {
    margin: 0;
    padding: 0;
    overflow: hidden;
    background: var(--paper);
  }
  .poster {
    position: relative;
    width: 960px;
    height: 1200px;
    overflow: hidden;
    background: var(--paper);
    font-family: "Montserrat", sans-serif;
  }
  .backdrop {
    position: absolute;
    inset: 0;
    width: 960px;
    height: 1200px;
  }
  .headline {
    position: absolute;
    left: 0;
    width: 960px;
    margin: 0;
    text-align: center;
    line-height: 1;
    white-space: nowrap;
  }
  .discount {
    top: 333px;
    font-size: 108px;
    font-weight: 600;
    color: var(--plum);
  }
  .occasion {
    top: 456px;
    font-size: 106px;
    font-weight: 400;
    letter-spacing: -1px;
    color: var(--orchid);
  }
  .sale-word {
    top: 570px;
    font-size: 106px;
    font-weight: 400;
    color: var(--orchid);
  }
  .detox {
    top: 698px;
    font-size: 75px;
    font-weight: 700;
    color: var(--plum);
  }
  .tagline {
    top: 796px;
    font-family: "Crimson Text", serif;
    font-size: 66px;
    font-weight: 400;
    color: var(--orchid);
  }
</style>
</head>
<body>
<main class="poster">
  <svg class="backdrop" viewBox="0 0 1080 1350" aria-hidden="true">
    <defs>
      <linearGradient id="pattern-fade-tl" x1="0" y1="0" x2="1" y2="1">
        <stop offset="0" stop-color="#e6c8e6" stop-opacity="0.45"/>
        <stop offset="1" stop-color="#e6c8e6" stop-opacity="0"/>
      </linearGradient>
      <linearGradient id="pattern-fade-br" x1="1" y1="1" x2="0" y2="0">
        <stop offset="0" stop-color="#e6c8e6" stop-opacity="0.45"/>
        <stop offset="1" stop-color="#e6c8e6" stop-opacity="0"/>
      </linearGradient>
    </defs>

    <!-- frame -->
    <rect class="frame" x="0" y="0" width="1080" height="1350" fill="var(--plum)"/>
    <rect class="frame-inner" x="16" y="16" width="1048" height="1319" fill="var(--paper)"/>

    <!-- decorative line-pattern areas -->
    <rect class="pattern-area" role="img" aria-label="Faint lilac geometric cube line pattern" x="16" y="16" width="340" height="330" fill="url(#pattern-fade-tl)"/>
    <rect class="pattern-area" role="img" aria-label="Faint lilac geometric cube line pattern" x="580" y="865" width="484" height="470" fill="url(#pattern-fade-br)"/>

    <!-- corner blobs -->
    <path class="blob" d="M708 16 C745 50 820 55 880 85 C930 115 935 180 970 215 C1000 245 1040 250 1064 250 V16 Z" fill="var(--orchid)"/>
    <path class="blob" d="M16 1072 C60 1072 90 1110 120 1140 C160 1185 220 1180 280 1175 C360 1170 395 1240 390 1335 H16 Z" fill="var(--orchid)"/>

    <!-- corner circles -->
    <circle class="dot" cx="16" cy="16" r="106" fill="var(--orchid)"/>
    <circle class="dot-inner" cx="16" cy="16" r="64" fill="var(--orchid-light)"/>
    <circle class="dot" cx="1064" cy="1335" r="90" fill="var(--orchid)"/>
    <circle class="dot-inner" cx="1064" cy="1335" r="50" fill="var(--orchid-light)"/>

    <!-- re-draw frame edges over circles -->
    <path d="M0 0 H1080 V1350 H0 Z M16 16 V1335 H1064 V16 Z" fill="var(--plum)" fill-rule="evenodd"/>
  </svg>

  <h1 class="headline discount">25% OFF</h1>
  <p class="headline occasion">MOTHER’S DAY</p>
  <p class="headline sale-word">SALE</p>
  <h2 class="headline detox">DETOX THIS SPRING</h2>
  <p class="headline tagline">Shine This Summer</p>
</main>
</body>
</html>
```